Corinnehabbard.com

1. Conceptualization and designing of the site Homepage. The Homepage design will be completely customized and based on your design instructions (i.e. preferred colors, links to reference sites that you want us to take reference from if any etc) and the recently completed logo design.
2. Upon homepage design approval, based on it we will be creating the layout for the other 4 site inner pages (i.e. About page, Contact page, Services page, and Insights (publications, media).
3. Once all the inner page designs are approved, we will get the designs built (will make sure that the site is completely Responsive - works on all devices) within your provided WIX account.
4. We will add the static text and images provided by you to the Home page, About page, Contact page, and the Services page. For the 2 Insights sub-pages, we will add 1-2 sample Publications and Media entries.
once you confirm the total number of required entries for the 2 sub-pages, I will accordingly quote you on the same
5. Integration of a Contact form on the Contact page that will email the filled in details to your mail id.

```html
<!DOCTYPE html>
<html lang="en">
<head>
<meta charset="utf-8">
<title>Corinne Habbard Consulting</title>
<link href="https://fonts.googleapis.com/css2?family=Jost:wght@400;500;600&family=Roboto:wght@400;500;700&display=swap" rel="stylesheet">
<style>
:root{
  --blue:#1ba6e4;--blue-light:#5ccdf6;--navy:#0c3b52;--green:#1e8b3a;
  --red:#e8141b;--orange:#f7941d;--ink:#111;--grey:#777;--black:#000;
}
*{box-sizing:border-box;margin:0;padding:0}
html,body{width:1200px;height:4221px;overflow:hidden}
body{font-family:"Roboto",sans-serif;color:var(--ink);background:#fff;position:relative}
.abs{position:absolute}
.head{font-family:"Jost",sans-serif;font-weight:500}
.btn{position:absolute;display:flex;align-items:center;justify-content:center;gap:8px;color:#fff;font-weight:700;font-size:14px;border-radius:30px;background:linear-gradient(90deg,var(--red),var(--orange))}
.btn i{width:14px;height:14px;border-radius:50%;background:#fff;display:inline-block}
section{position:absolute;left:0;width:1200px;overflow:hidden}

/* top bar */
.topbar{top:0;height:48px;background:var(--blue)}
.social{position:absolute;top:10px;width:28px;height:28px;border-radius:50%;background:#fff}
.contact-item{position:absolute;top:0;height:48px;display:flex;align-items:center;gap:14px;color:#fff;font-size:14px;font-weight:500}
.contact-item b{width:30px;height:30px;border-radius:50%;background:#fff;display:flex;align-items:center;justify-content:center}
.divider{position:absolute;left:846px;top:0;width:1px;height:48px;background:rgba(255,255,255,.6)}

/* hero */
.hero{top:48px;height:670px;background:linear-gradient(100deg,#fff 40%,#fde9ec 100%)}
.nav{position:absolute;left:492px;top:0;width:708px;height:64px;background:var(--black);border-radius:32px 0 0 32px;display:flex;align-items:center;gap:56px;padding-left:60px;color:#fff;font-size:14px;font-weight:500}
.brand{position:absolute;display:flex;flex-direction:column;align-items:center;font-family:"Roboto",sans-serif;font-weight:500;color:var(--blue)}
.brand .mark{width:56px;height:56px;border-radius:50%;border:2px solid #bbb;margin-bottom:6px}
.hero-photo{position:absolute;left:560px;top:0;width:530px;height:580px;border-radius:0 0 260px 300px;background:linear-gradient(160deg,#6b6f76,#c77b4a 55%,#e9e3dc);border-right:8px solid var(--orange);border-bottom:8px solid var(--orange)}
.welcome{left:115px;top:155px;font-size:20px}
.hero-title{left:112px;top:185px;font-size:68px;line-height:74px;color:var(--navy);font-family:"Jost",sans-serif;font-weight:500}
.hero-title span{color:var(--green)}
.hero-text{left:110px;top:422px;width:440px;font-size:15px;line-height:25px;font-weight:500}
.card{position:absolute;background:#fff;border-radius:10px;box-shadow:0 6px 16px rgba(0,0,0,.15)}

/* about */
.about{top:718px;height:650px;background:#f7f7f8}
.about-photo{position:absolute;left:167px;top:90px;width:303px;height:438px;border-radius:34px;background:linear-gradient(170deg,#7a5135,#3a2a24 60%,#6c8b96)}
.about h2{left:633px;top:172px;font-size:44px}
.about p{left:633px;top:242px;width:452px;font-size:13px;line-height:26px;color:var(--grey)}

/* services */
.services{top:1368px;height:596px;background:linear-gradient(180deg,var(--blue-light),var(--blue))}
.sec-title{position:absolute;left:0;width:1200px;text-align:center;font-size:42px;color:#fff}
.svc{position:absolute;top:176px;width:272px;height:303px;background:#fff;border-radius:24px;text-align:center;padding-top:40px;box-shadow:0 8px 20px rgba(0,0,0,.15)}
.svc h3{font-size:18px;font-weight:700;margin-top:20px}
.svc hr{width:60px;border:0;border-top:3px solid var(--ink);margin:12px auto 26px}
.svc p{font-size:13px;line-height:26px;color:var(--grey);padding:0 30px}

/* stats */
.stats{top:1964px;height:288px;background:#fff}
.stat{position:absolute;top:110px;display:flex;gap:16px}
.stat .ic{width:64px;height:64px;border-radius:50%;background:#f1f1f1;margin-top:8px}
.stat strong{display:block;font-size:32px;font-weight:500}
.stat small{display:block;font-size:13px;font-weight:700;line-height:24px}

/* clients */
.clients{top:2252px;height:458px;background:linear-gradient(100deg,#eef6fb,#fdeee8)}
.clients h2{left:0;width:1200px;text-align:center;top:80px;font-size:40px}
.review{position:absolute;top:175px;width:420px;height:200px;background:#fff;border-radius:40px;border-left:2px solid var(--red);border-bottom:2px solid var(--orange);padding:28px 40px 0 104px}
.review h4{font-size:16px;font-weight:700;display:flex;justify-content:space-between}
.review h4 span{color:var(--orange);letter-spacing:3px}
.review p{font-size:13px;line-height:26px;color:var(--grey);margin-top:18px;text-align:justify}
.avatar{position:absolute;width:120px;height:120px;border-radius:50%;background:linear-gradient(#dfe3e8,#36414f)}
.arrow{position:absolute;width:58px;height:58px;border-radius:50%;background:linear-gradient(135deg,var(--red),var(--orange));color:#fff;display:flex;align-items:center;justify-content:center;font-size:20px}

/* blog */
.blog{top:2710px;height:558px;background:linear-gradient(180deg,var(--blue-light),var(--blue))}
.post{position:absolute;top:175px;width:279px;height:295px;background:#fff;border-left:8px solid #fff}
.post .img{height:174px;margin:6px 0 0;background:linear-gradient(160deg,#9aa4ae,#3d4650)}
.post h4{font-size:15px;font-weight:500;line-height:22px;padding:20px 20px 0}
.post p{font-size:12px;line-height:22px;color:var(--grey);padding:4px 20px 0}
.date{position:absolute;top:-30px;right:16px;width:66px;height:108px;border-radius:33px;background:linear-gradient(180deg,var(--orange),var(--red));color:#fff;font-family:"Jost",sans-serif;font-size:22px;font-weight:500;text-align:center;padding-top:12px;line-height:28px}

/* contact */
.contact{top:3268px;height:517px;background:#fff}
.contact h2{left:0;width:1200px;text-align:center;top:78px;font-size:42px}
.field{position:absolute;background:#fff;border-radius:28px;box-shadow:0 4px 14px rgba(0,0,0,.1);font-size:11px;color:#555;padding:22px 28px}

/* footer */
.footer{top:3785px;height:436px;background:var(--black);color:#fff}
.footer h5{position:absolute;top:132px;font-size:14px;font-weight:700}
.links{position:absolute;top:168px;font-size:13px;line-height:32px;list-style:none}
</style>
</head>
<body>

<section class="topbar">
  <span class="social" style="left:170px" aria-label="Social profile"></span>
  <span class="social" style="left:208px" aria-label="Social profile"></span>
  <span class="social" style="left:246px" aria-label="Social profile"></span>
  <div class="contact-item" style="left:598px"><b><svg width="14" height="10"><rect width="14" height="10" rx="1" fill="#1ba6e4"/><path d="M0 0l7 6 7-6" stroke="#fff" fill="none"/></svg></b>info@corinnehabbard.com</div>
  <span class="divider"></span>
  <div class="contact-item" style="left:872px"><b><svg width="14" height="14" viewBox="0 0 24 24"><path fill="#1ba6e4" d="M6.6 10.8a15 15 0 006.6 6.6l2.2-2.2c.3-.3.7-.4 1-.2 1.1.4 2.3.6 3.6.6.6 0 1 .4 1 1V20c0 .6-.4 1-1 1A17 17 0 013 4c0-.6.4-1 1-1h3.5c.6 0 1 .4 1 1 0 1.3.2 2.5.6 3.6.1.3 0 .7-.2 1z"/></svg></b>+1 (8888) 888 888</div>
</section>

<section class="hero">
  <div class="hero-photo" role="img" aria-label="Photo of a smiling consultant talking at a desk with a laptop"></div>
  <nav class="nav"><span>Home</span><span>About Us</span><span>Insights</span><span>Services</span><span>Contact Us</span>
    <svg width="14" height="14"><circle cx="6" cy="6" r="4.5" stroke="#fff" stroke-width="2" fill="none"/><path d="M9 9l4 4" stroke="#fff" stroke-width="2"/></svg></nav>
  <div class="brand" style="left:118px;top:8px"><span class="mark"></span><span style="font-size:15px">CORINNE HABBARD</span><span style="font-size:11px;letter-spacing:3px">CONSULTING</span></div>
  <div class="abs welcome">Welcome To</div>
  <div class="abs hero-title">CORINNE<br>HABBARD<br><span>CONSULTING</span></div>
  <p class="abs hero-text">Sed ut perspiciatis unde omnis iste natus error sit voluptatem accusantium doloremque laudantium, totam</p>
  <div class="btn" style="left:115px;top:506px;width:165px;height:42px">GET STARTED <i></i></div>
  <div class="card" style="left:584px;top:422px;width:98px;height:137px;text-align:center;font-size:9px;padding-top:16px">
    <span class="abs" style="left:6px;top:2px;font-size:12px">×</span>
    <svg width="48" height="48" viewBox="0 0 48 48"><circle cx="24" cy="24" r="22" fill="#f7b21d"/><path d="M24 24V2a22 22 0 0122 22z" fill="#e8141b"/><circle cx="24" cy="24" r="9" fill="#fff"/></svg>
    <div style="margin-top:18px">Lorem ipsum dolor</div><div style="margin-top:8px">Sed ut</div>
  </div>
  <div class="card" style="left:784px;top:550px;width:142px;height:74px">
    <svg width="142" height="74"><polyline points="30,50 56,24 76,48 104,40" fill="none" stroke="#0c3b52" stroke-width="3"/><circle cx="30" cy="50" r="4" fill="#fff" stroke="#0c3b52" stroke-width="2"/><circle cx="76" cy="48" r="4" fill="#fff" stroke="#0c3b52" stroke-width="2"/><circle cx="104" cy="40" r="4" fill="#fff" stroke="#0c3b52" stroke-width="2"/></svg>
  </div>
</section>

<section class="about">
  <div class="abs" style="left:105px;top:330px;width:290px;height:290px;border-radius:50%;background:linear-gradient(var(--blue-light),var(--blue))"></div>
  <div class="about-photo" role="img" aria-label="Portrait of the consultant seated in an armchair"></div>
  <div class="abs" style="left:418px;top:128px;width:104px;height:104px;border-radius:50%;background:#fff;box-shadow:0 6px 16px rgba(0,0,0,.2)"><div style="margin:10px;width:84px;height:84px;border-radius:50%;background:linear-gradient(var(--blue-light),var(--blue))"></div></div>
  <h2 class="abs head">ABOUT US</h2>
  <p class="abs">Lorem ipsum dolor sit amet, consectetur adipiscing elit, sed do eiusmod tempor incididunt ut labore et dolore magna aliqua. Ut enim ad minim veniam, quis nostrud exercitation ullamco laboris nisi ut aliquip ex ea commodo consequat. Duis aute irure dolor in reprehenderit in voluptate velit esse cillum dolore eu fugiat nulla pariatur. Excepteur sint occaecat cupidatat non proident, sunt in culpa</p>
  <div class="btn" style="left:633px;top:420px;width:165px;height:42px">LEARN MORE <i></i></div>
</section>

<section class="services">
  <div class="abs" style="left:144px;top:0;width:146px;height:146px;border-radius:50%;background:rgba(27,166,228,.5)"></div>
  <h2 class="sec-title head" style="top:80px">OUR SERVICES</h2>
  <div class="svc" style="left:121px"><svg width="60" height="56"><rect x="6" y="0" width="18" height="14" rx="2" fill="#e8141b"/><rect x="34" y="0" width="20" height="14" rx="2" fill="#f7941d"/><circle cx="16" cy="28" r="7" fill="#e8141b"/><circle cx="44" cy="28" r="7" fill="#f7941d"/><path d="M2 56a14 14 0 0128 0zM30 56a14 14 0 0128 0z" fill="#e8141b"/></svg><h3>Consultancy &amp; Advising</h3><hr><p>Lorem ipsum dolor sit amet, consectetur adipiscing elit, sed do eiusmod tempor incididunt</p></div>
  <div class="svc" style="left:464px;border-bottom:4px solid var(--red)"><svg width="60" height="56"><circle cx="30" cy="22" r="16" fill="#f7941d"/><circle cx="30" cy="22" r="7" fill="#fff"/><rect x="22" y="42" width="16" height="5" fill="#e8141b"/><rect x="24" y="50" width="12" height="5" fill="#e8141b"/></svg><h3>Problem Solving</h3><hr><p>Lorem ipsum dolor sit amet, consectetur adipiscing elit, sed do eiusmod tempor incididunt</p>
    <div class="arrow" style="left:108px;top:280px">›</div></div>
  <div class="svc" style="left:805px"><svg width="60" height="56"><rect x="20" y="0" width="20" height="12" rx="3" fill="#e8141b"/><circle cx="30" cy="22" r="10" fill="#f7941d"/><path d="M12 56a18 18 0 0136 0z" fill="#e8141b"/></svg><h3>Training of Registered Nurse</h3><hr><p>Lorem ipsum dolor sit amet, consectetur adipiscing elit, sed do eiusmod tempor incididunt</p></div>
</section>

<section class="stats">
  <div class="stat" style="left:111px"><span class="ic"></span><div><strong>10K</strong><small>CLEARANCE<br>HAPPY CUSTOMERS</small></div></div>
  <div class="stat" style="left:365px"><span class="ic"></span><div><strong>18+</strong><small>YEARS OF<br>EXPERIENCES</small></div></div>
  <div class="stat" style="left:620px"><span class="ic"></span><div><strong>100K</strong><small>PROFESSIONAL<br>ADVISORS</small></div></div>
  <div class="stat" style="left:874px"><span class="ic"></span><div><strong>3060+</strong><small>CASES<br>EVERY YEARS</small></div></div>
</section>

<section class="clients">
  <h2 class="abs head">OUR CLIENTS SAY'S</h2>
  <div class="review" style="left:154px"><h4>Jhony Markerny <span>★★★★★</span></h4><p>Sed ut perspiciatis unde omnis iste natus error sit voluptatem accusantium doloremque laudantium, totam rem aperiam, eaque ipsa quae ab illo</p></div>
  <div class="avatar" style="left:111px;top:212px" role="img" aria-label="Client portrait"></div>
  <div class="review" style="left:670px"><h4>Jhony Markerny <span>★★★★★</span></h4><p>Sed ut perspiciatis unde omnis iste natus error sit voluptatem accusantium doloremque laudantium, totam rem aperiam, eaque ipsa quae ab illo</p></div>
  <div class="avatar" style="left:627px;top:212px" role="img" aria-label="Client portrait"></div>
  <div class="arrow" style="left:18px;top:243px">‹</div>
  <div class="arrow" style="left:1123px;top:243px">›</div>
</section>

<section class="blog">
  <h2 class="sec-title head" style="top:78px">OUR BLOG</h2>
  <div class="post" style="left:111px"><div class="img" role="img" aria-label="Two colleagues reviewing a tablet"></div><h4>Lorem ipsum dolor sit amet, consectetur adipiscing elit, sed</h4><p>Lorem ipsum dolor sit amet, tur piscing elit, sed do eiusmod tempor incididunt</p><div class="date">APR<br>22</div></div>
  <div class="post" style="left:460px"><div class="img" role="img" aria-label="Meeting at an office table with a laptop"></div><h4>Lorem ipsum dolor sit amet, consectetur adipiscing elit, sed</h4><p>Lorem ipsum dolor sit amet, tur piscing elit, sed do eiusmod tempor incididunt</p><div class="date">APR<br>22</div></div>
  <div class="post" style="left:810px"><div class="img" role="img" aria-label="Business partners in discussion"></div><h4>Lorem ipsum dolor sit amet, consectetur adipiscing elit, sed</h4><p>Lorem ipsum dolor sit amet, tur piscing elit, sed do eiusmod tempor incididunt</p><div class="date">APR<br>22</div></div>
  <div class="arrow" style="left:18px;top:292px">‹</div>
  <div class="arrow" style="left:1123px;top:292px">›</div>
</section>

<section class="contact">
  <h2 class="abs head">CONTACT US</h2>
  <div class="field" style="left:243px;top:166px;width:344px;height:56px">NAME</div>
  <div class="field" style="left:243px;top:236px;width:344px;height:56px">EMAIL</div>
  <div class="field" style="left:243px;top:305px;width:344px;height:56px">PHONE</div>
  <div class="field" style="left:611px;top:166px;width:346px;height:195px">MESSAGE</div>
  <div class="btn" style="left:518px;top:392px;width:164px;height:42px">SUBMIT</div>
</section>

<section class="footer">
  <div class="brand" style="left:90px;top:60px;color:#fff"><span class="mark" style="border-color:#fff"></span><span style="font-size:15px">CORINNE HABBARD</span><span style="font-size:11px;letter-spacing:3px">CONSULTING</span></div>
  <p class="abs" style="left:90px;top:190px;width:260px;font-size:13px;line-height:25px">Lorem ipsum dolor sit amet, consectetur adipiscing elit, sed do eiusmod tempor incididunt ut labore et dolore magna</p>
  <div class="abs" style="left:90px;top:290px;width:276px;height:40px;border-radius:20px;background:linear-gradient(90deg,#fff 85%,var(--orange) 85%);font-size:11px;color:#555;padding:13px 22px">Enter Email<span class="abs" style="right:16px;top:11px;color:#fff">›</span></div>
  <h5 style="left:474px">EXPLORE</h5>
  <ul class="links" style="left:474px"><li>About Us</li><li>Projects</li><li>Contact us</li><li>Teams</li><li>Blog &amp; News</li></ul>
  <h5 style="left:654px">PRODUCTS</h5>
  <ul class="links" style="left:654px"><li>Capital Management</li><li>Quick Response</li><li>Flexible Payment</li><li>Consultancy</li></ul>
  <h5 style="left:859px">YOU'VE QUESTION?</h5>
  <svg class="abs" style="left:859px;top:172px" width="40" height="40" viewBox="0 0 24 24"><path fill="none" stroke="#fff" stroke-width="1.2" d="M6.6 10.8a15 15 0 006.6 6.6l2.2-2.2c.3-.3.7-.4 1-.2 1.1.4 2.3.6 3.6.6.6 0 1 .4 1 1V20c0 .6-.4 1-1 1A17 17 0 013 4c0-.6.4-1 1-1h3.5c.6 0 1 .4 1 1 0 1.3.2 2.5.6 3.6.1.3 0 .7-.2 1z"/></svg>
  <div class="abs" style="left:920px;top:173px;font-size:12px;color:var(--orange);font-weight:500">You've question?</div>
  <div class="abs" style="left:920px;top:194px;font-size:16px;font-weight:700">+1 (8888) 888 888</div>
  <svg class="abs" style="left:864px;top:238px" width="38" height="34"><rect x="1" y="8" width="36" height="25" fill="none" stroke="#fff" stroke-width="1.4"/><path d="M1 8l18 14 18-14" fill="none" stroke="#fff" stroke-width="1.4"/></svg>
  <div class="abs" style="left:920px;top:238px;font-size:12px;color:var(--orange);font-weight:500">Email Us</div>
  <div class="abs" style="left:920px;top:259px;font-size:16px;font-weight:700">info@corinnehabbard.com</div>
  <div class="abs" style="left:0;width:1200px;top:362px;text-align:center;font-size:10px">Copyright@2024 - Corinne Habbard Consulting . All Rights Reserved</div>
</section>

</body>
</html>
```